Letter and Envelope Design For Harborline Realty

Please design a letter and an envelope incorporating our logo (See Attached). We are also launched a business card contest. Since we want them to match, please feel free to submit a design for both the business card and also the letter design and envelope.

Requirements
Must have
• The envelope, the letter and the business cards must match somehow connecting the designs. We want them to have something that holds them together besides the logo.

```html
<!DOCTYPE html>
<html lang="en">
<head>
<meta charset="utf-8">
<title>Harborline Realty – Letterhead and Envelopes</title>
<link href="https://fonts.googleapis.com/css2?family=Questrial&family=Roboto:wght@400;500&display=swap" rel="stylesheet">
<style>
  :root {
    --backdrop: #dcdcdc;
    --paper: #f7f7f7;
    --brand-blue: #0b1a8c;
    --ink: #4a4a4a;
    --ink-soft: #5c5c5c;
    --ghost: #e6e7ee;
    --rule: #c9c9c9;
  }
  * { box-sizing: border-box; margin: 0; padding: 0; }
  html, body { width: 1200px; height: 877px; overflow: hidden; background: var(--backdrop); }
  .canvas { position: relative; width: 1200px; height: 877px; }
  .sheet {
    position: absolute; background: var(--paper);
    box-shadow: 0 2px 10px rgba(0,0,0,.12);
    overflow: hidden;
  }
  .letterhead { left: 69px; top: 64px; width: 527px; height: 742px; }
  .ghost-ring { position: absolute; border-radius: 50%; border: 12px solid var(--ghost); }
  .letterhead .ghost-ring { left: 112px; top: 221px; width: 304px; height: 304px; }

  .brand { position: absolute; text-align: center; font-family: "Roboto", sans-serif; font-weight: 500; color: var(--brand-blue); }
  .brand-mark { display: block; margin: 0 auto 6px; border: 2px solid var(--brand-blue); border-radius: 50%; }
  .brand-name { display: block; line-height: 1.15; }
  .letterhead .brand { left: 46px; top: 44px; width: 128px; }
  .letterhead .brand-mark { width: 46px; height: 46px; }
  .letterhead .brand-name { font-size: 13px; letter-spacing: 1.4px; }
  .letterhead .brand-name.sub { font-size: 9px; letter-spacing: 3px; }

  .contact {
    position: absolute; left: 374px; top: 48px; padding-left: 14px;
    border-left: 1px solid var(--rule); height: 70px;
    font-family: "Roboto", sans-serif; font-size: 8px; color: var(--ink); line-height: 10px;
  }
  .contact .address { margin-top: 2px; margin-bottom: 3px; }
  .contact-line { display: flex; align-items: center; gap: 5px; height: 10.5px; }
  .contact-line svg { width: 7px; height: 7px; fill: var(--brand-blue); }

  .letter-body { position: absolute; left: 46px; top: 211px; width: 439px; font-family: "Questrial", sans-serif; color: var(--ink); }
  .salutation { font-size: 13.6px; margin-bottom: 20px; }
  .letter-body p { font-size: 7.6px; line-height: 11.4px; margin-bottom: 11.5px; text-align: justify; }
  .closing { position: absolute; left: 46px; top: 486px; font-family: "Questrial", sans-serif; font-size: 7.6px; color: var(--ink); }
  .signature { position: absolute; left: 41px; top: 520px; width: 94px; height: 38px; background: linear-gradient(90deg, #d9dcf0, #eceef7); border-radius: 3px; }

  .footer-web { position: absolute; left: 51px; top: 696px; font-family: "Roboto", sans-serif; font-size: 7.8px; letter-spacing: 1.6px; font-weight: 500; color: var(--brand-blue); }
  .footer-rule { position: absolute; left: 46px; top: 709px; width: 439px; height: 1px; background: var(--brand-blue); }
  .footer-rule::before { content: ""; position: absolute; left: 0; top: -1px; width: 108px; height: 3px; background: var(--brand-blue); }

  .envelope-back { left: 614px; top: 269px; width: 531px; height: 241px; }
  .envelope-flap { position: absolute; left: 0; top: 0; width: 531px; height: 74px; }
  .flap-brand { position: absolute; left: 0; top: 30px; width: 531px; text-align: center; font-family: "Roboto", sans-serif; font-weight: 500; font-size: 10px; letter-spacing: 2px; color: #fff; }

  .envelope-front { left: 614px; top: 563px; width: 533px; height: 242px; }
  .envelope-front .ghost-ring { left: 316px; top: 23px; width: 194px; height: 194px; border-width: 8px; }
  .envelope-front .brand { left: 28px; top: 26px; width: 106px; }
  .envelope-front .brand-mark { width: 40px; height: 40px; margin-bottom: 5px; }
  .envelope-front .brand-name { font-size: 11px; letter-spacing: 1.2px; }
  .envelope-front .brand-name.sub { font-size: 7.5px; letter-spacing: 2.6px; }
  .return-address { position: absolute; left: 28px; top: 95px; width: 106px; text-align: center; font-family: "Roboto", sans-serif; font-size: 8px; line-height: 10px; color: var(--ink-soft); }
</style>
</head>
<body>
<main class="canvas">

  <section class="sheet letterhead">
    <div class="ghost-ring"></div>

    <div class="brand">
      <span class="brand-mark"></span>
      <span class="brand-name">HARBORLINE</span>
      <span class="brand-name sub">REALTY</span>
    </div>

    <address class="contact">
      <div class="address">2140 Tidewater Road<br>Juneau, Alaska 99801</div>
      <div class="contact-line"><svg viewBox="0 0 10 10"><path d="M2 0.5l2 2-1 1.3c.7 1.4 1.8 2.5 3.2 3.2l1.3-1 2 2-1.2 1.5C4.5 9.2.8 5.5.5 1.7z"/></svg>555 210 4471</div>
      <div class="contact-line"><svg viewBox="0 0 10 10"><path d="M2.5 0h5v10h-5zM3.5 1v7h3V1z"/></svg>555 384 1902</div>
      <div class="contact-line"><svg viewBox="0 0 10 10"><path d="M2 0h6v3H2zM0 3.5h10v5H0zM2 7h6v3H2z"/></svg>555 672 3085</div>
      <div class="contact-line"><svg viewBox="0 0 10 10"><path d="M0 2h10v6H0zM0.8 2.6 5 5.6l4.2-3z" fill-rule="evenodd"/></svg>hello@harborline.com</div>
    </address>

    <article class="letter-body">
      <p class="salutation">Dear Mr. Carter,</p>
      <p>Lorem ipsum dolor sit amet, consectetur adipiscing elit. Donec orci purus, luctus vitae dignissim eu, iaculis sed purus. Vivamus faucibus, ipsum nec aliquet viverra, leo mauris condimentum ligula, sit amet sagittis enim ligula quis arcu. Nam egestas tortor id nisi porttitor mattis. In tortor ante, ultricies in suscipit a, tempus non massa. Vivamus et auctor mi. Fusce vel massa nulla. Phasellus nec eros mauris, et scelerisque orci.</p>
      <p>Donec malesuada orci vitae nulla accumsan porta a id massa. Quisque accumsan iaculis magna sit amet fringilla. Maecenas consequat, magna eget tincidunt semper, odio nibh rutrum mi, id feugiat ante nisi eu risus. Vestibulum nunc orci, rhoncus a placerat in, ultricies in mi. Cras mattis varius eros, vel fringilla nisi suscipit eget. Quisque scelerisque sagittis nulla at porttitor.</p>
      <p>Sed id augue vitae urna euismod commodo aliquet a quam. Pellentesque arcu velit, cursus et malesuada ut, consequat et diam. Nullam erat sem, rhoncus id ullamcorper vitae, rhoncus et arcu. In ultricies ultricies nulla, ut rutrum nisi iaculis at. Donec eu magna a metus ornare faucibus. Fusce aliquet faucibus ultricies. Morbi semper, est id tincidunt gravida, sem arcu adipiscing lacus, ac bibendum nulla leo eu purus. Quisque nec diam sed risus consectetur a accumsan quis quis nibh. Vestibulum id purus lorem.</p>
      <p>It is a long established fact that a reader will be distracted by the readable content of a page when looking at its layout. The point of using Lorem Ipsum is that it has a more-or-less normal distribution of letters, as opposed to using 'Content here, content here', making it look like readable English. Many desktop publishing packages</p>
    </article>

    <p class="closing">Sincerely,</p>
    <div class="signature" role="img" aria-label="Handwritten signature of Dana Carter"></div>

    <div class="footer-web">www.harborline.com</div>
    <div class="footer-rule"></div>
  </section>

  <section class="sheet envelope-back">
    <svg class="envelope-flap" viewBox="0 0 531 74" aria-hidden="true">
      <path d="M0 0H531L523 42Q517 74 489 74H42Q14 74 8 42Z" fill="#0b1a8c"/>
    </svg>
    <div class="flap-brand">HARBORLINE REALTY</div>
  </section>

  <section class="sheet envelope-front">
    <div class="ghost-ring"></div>
    <div class="brand">
      <span class="brand-mark"></span>
      <span class="brand-name">HARBORLINE</span>
      <span class="brand-name sub">REALTY</span>
    </div>
    <address class="return-address">2140 Tidewater Road<br>Juneau, Alaska 99801</address>
  </section>

</main>
</body>
</html>
```